A Brochure to sell LED Downlights to clients

I am starting a campaign on google for LED down lights the link to the landing page can be found at brinholt.com.au/led .

When the client send a contact request i want to be able to send back a brochure of a picture of each light (Approx 6 - 8 types) and have a few sentences on each light and price brake down.

'Quarnel Ostrava 9w LED'

**Information**

1-10 lights $49
11-20 lights $45
21 - 40 lights $42
40 and over $40

EACH LIGHT:

Hi,

This is very good.

I
But,

Each light will have its own price.

Can i get it made like this;

Picture - Spec - Pricing in a table style please? - i like the layout it just need to suit the tables under:

picture - Brand - Price 1-10
Model - Price 11-20
Watts - Price 21-21
lumen - price 30- 40
Warranty = price 40+

Model - Price 11-20
Watts - Price 21-21
lumen - price 30- 40
Warranty = price 40+

Model - Price 11-20
Watts - Price 21-21
lumen - price 30- 40
Warranty = price 40+

and so on....

I want it to be on Microsoft Word so i can easily chop and edit the prices and images also. (So i can print to PDF)

For more information see my website to seek inspiration. I have a zip file of my logo for actual creation and should be also to source pictures of the lights when finalising the design.

brinholt.com.au

Thanks

Added 2 x additional Dimmers please see zip file, same layout/pricing as the downlights

Target Market(s)

Homeowners/commercial business owners

Industry/Entity Type

Electric Company

Font styles to use
Sans Serif

Colors
86cfc6
ffffff
000000

Requirements
Must have
• Professional looking, Colours to the theme of my logo/website
Nice to have
• An awesome design that sells it's self!!!!!!!
• My Logo font is 'Radikil" it would be nice to follow that theme if it doesn't look good i am open to have a nice legible font for the copy.
Should not have
• Cheesy light globes or images

```html
<!DOCTYPE html>
<html lang="en">
<head>
<meta charset="utf-8">
<title>Brinholt LED Downlights Catalog</title>
<link href="https://fonts.googleapis.com/css2?family=Jost:wght@400;500;600;700&display=swap" rel="stylesheet">
<style>
:root{
  --stage:#333333;
  --teal:#00a99d;
  --teal-soft:#86cfc6;
  --ink:#3b3b3b;
  --slate:#4a4a4a;
  --paper:#ffffff;
  --mist:#ececec;
}
*{box-sizing:border-box;margin:0;padding:0}
html,body{width:1200px;height:2980px;overflow:hidden}
body{background:var(--stage);font-family:"Jost",sans-serif;position:relative;color:var(--ink)}
.page{position:absolute;left:290px;width:622px;height:880px;overflow:hidden}

/* cover */
.cover{top:95px;background:var(--paper)}
.cover-backdrop{position:absolute;inset:0;background:linear-gradient(180deg,#f4f4f4 0%,#e9e8e6 45%,#f2f2f2 70%,#fafafa 100%)}
.cover-title{position:absolute;right:30px;top:108px;text-align:right;line-height:1}
.cover-title .word{display:block;font-size:48px;font-weight:400;color:var(--teal);letter-spacing:1px}
.cover-title .years{display:block;font-size:46px;font-weight:400;color:var(--slate);margin-top:2px}
.tile{position:absolute}
.tile-dark{left:132px;top:254px;width:180px;height:170px;background:#505050}
.tile-kitchen{left:318px;top:254px;width:304px;height:170px;background:linear-gradient(135deg,#5a3a22,#9a6a3e 50%,#d8c6a4)}
.tile-boardroom{left:0;top:430px;width:126px;height:174px;background:linear-gradient(160deg,#3a2c1e,#8a6a3a 55%,#c9b58a)}
.tile-dining{left:132px;top:430px;width:180px;height:174px;background:linear-gradient(150deg,#b9a58a,#7a5a3a 50%,#d9d3c8)}
.tile-brand{left:318px;top:430px;width:180px;height:174px;background:var(--teal);display:flex;align-items:center;justify-content:center}
.brand-name{font-family:"Jost",sans-serif;font-weight:500;color:var(--paper);display:flex;align-items:center;gap:8px}
.brand-name .mark{width:12px;height:12px;background:var(--paper);display:inline-block}
.tile-brand .brand-name{font-size:34px}
.cover-url{position:absolute;left:0;right:0;top:818px;text-align:center;font-size:22px;font-weight:500;letter-spacing:1px;color:var(--slate)}

/* product sheet */
.sheet{top:1069px;background:var(--paper)}
.sheet-backdrop{position:absolute;inset:0;background:linear-gradient(180deg,#f6f6f6 0%,#e6e6e6 50%,#efefef 80%,#ffffff 90%)}
.sheet-heading{position:absolute;left:0;right:0;top:32px;text-align:center;font-size:26px;font-weight:700;color:var(--teal);letter-spacing:1px}
.product{position:absolute;left:88px;width:518px;height:126px;background:var(--paper);border:2px solid var(--teal);border-radius:20px}
.product-photo{position:absolute;left:18px;width:124px;height:124px;border-radius:50%}
.photo-white{background:radial-gradient(circle at 50% 45%,#ffffff 35%,#d8d8d8 60%,#a8a8a8 75%,transparent 77%)}
.photo-bronze{background:radial-gradient(circle at 50% 45%,#8a7a6a 20%,#4a3a2e 45%,#2a2a2a 62%,transparent 64%)}
.photo-steel{background:radial-gradient(circle at 50% 45%,#f0f0f0 32%,#b8b0a8 50%,#7a7670 66%,transparent 68%)}
.product-name{position:absolute;left:60px;top:12px;font-size:23px;font-weight:500;color:var(--teal);text-decoration:underline;text-underline-offset:3px}
.features{position:absolute;left:60px;top:48px;width:440px;display:grid;grid-template-columns:224px 210px;row-gap:6px;list-style:none}
.features li{position:relative;padding-left:20px;font-size:12px;line-height:15px;color:var(--ink)}
.features li::before{content:"";position:absolute;left:0;top:2px;width:11px;height:11px;border-radius:50%;background:var(--teal)}
.price-tab{position:absolute;left:188px;top:718px;width:280px;height:28px;background:var(--teal);color:var(--paper);font-size:18px;font-weight:500;text-align:center;line-height:28px}
.price-table{position:absolute;left:28px;top:746px;width:576px;height:92px;background:var(--slate);border:3px solid var(--teal);border-radius:18px;padding:12px 40px;display:grid;grid-template-columns:1fr 1fr;row-gap:4px;column-gap:20px}
.price-table div{font-size:21px;color:var(--paper);line-height:30px;white-space:nowrap}
.price-table span{color:var(--teal-soft)}
.price-table .right{padding-left:90px}
.sheet-url{position:absolute;right:30px;top:850px;font-size:16px;color:var(--slate)}

/* back cover */
.back{top:2025px;height:878px;background:var(--teal)}
.back-band{position:absolute;left:0;top:0;width:100%;height:16px;background:#8c8c8c}
.back-backdrop{position:absolute;left:0;top:16px;right:0;bottom:0;background:linear-gradient(180deg,#0fa99c 0%,#16a195 40%,#0c9d90 60%,#12a89b 100%)}
.back .brand-name{position:absolute;left:0;right:0;top:310px;justify-content:center;font-size:40px}
.back .brand-name .mark{width:14px;height:14px}
.back-url{position:absolute;left:0;right:0;top:820px;text-align:center;font-size:22px;font-weight:600;letter-spacing:1px;color:var(--paper)}
</style>
</head>
<body>

<section class="page cover">
  <div class="cover-backdrop" role="img" aria-label="Faded photo of a bright modern kitchen with downlights"></div>
  <h1 class="cover-title"><span class="word">CATALOG</span><span class="years">2017-2018</span></h1>
  <div class="tile tile-dark"></div>
  <div class="tile tile-kitchen" role="img" aria-label="Timber kitchen lit by LED downlights"></div>
  <div class="tile tile-boardroom" role="img" aria-label="Boardroom with recessed ceiling lights"></div>
  <div class="tile tile-dining" role="img" aria-label="Dining area and kitchen with downlights"></div>
  <div class="tile tile-brand"><span class="brand-name"><span class="mark"></span>brinholt</span></div>
  <p class="cover-url">www.brinholt.com.au</p>
</section>

<section class="page sheet">
  <div class="sheet-backdrop" role="img" aria-label="Faint photo of a lit interior"></div>
  <h2 class="sheet-heading">CHOOSE YOUR STYLE OF LED DOWNLIGHTS</h2>

  <article class="product" style="top:74px">
    <h3 class="product-name">Lorem ipsum dolor</h3>
    <ul class="features">
      <li>Save 80% on your energy bills with LEDs</li><li>Up to 7 years manufacturer's warranty</li>
      <li>50,000 hours of life</li><li>Brighter than halogen downlights</li>
    </ul>
  </article>
  <div class="product-photo photo-white" style="top:74px" role="img" aria-label="White LED downlight with heat-sink fins"></div>

  <article class="product" style="top:238px">
    <h3 class="product-name">Lorem ipsum dolor</h3>
    <ul class="features">
      <li>Save 80% on your energy bills with LEDs</li><li>Up to 7 years manufacturer's warranty</li>
      <li>50,000 hours of life</li><li>Brighter than halogen downlights</li>
    </ul>
  </article>
  <div class="product-photo photo-white" style="top:238px" role="img" aria-label="White LED downlight with driver cable"></div>

  <article class="product" style="top:398px">
    <h3 class="product-name">Lorem ipsum dolor</h3>
    <ul class="features">
      <li>Save 80% on your energy bills with LEDs</li><li>Up to 7 years manufacturer's warranty</li>
      <li>50,000 hours of life</li><li>Brighter than halogen downlights</li>
    </ul>
  </article>
  <div class="product-photo photo-bronze" style="top:398px" role="img" aria-label="Dark bronze LED downlight with driver"></div>

  <article class="product" style="top:558px">
    <h3 class="product-name">Lorem ipsum dolor</h3>
    <ul class="features">
      <li>Save 80% on your energy bills with LEDs</li><li>Up to 7 years manufacturer's warranty</li>
      <li>50,000 hours of life</li><li>Brighter than halogen downlights</li>
    </ul>
  </article>
  <div class="product-photo photo-steel" style="top:558px" role="img" aria-label="Brushed steel LED downlight"></div>

  <div class="price-tab">Quarnel Ostrava 9w LED</div>
  <div class="price-table">
    <div>1-10.......lights : <span>$49</span></div>
    <div class="right">21-40...lights : <span>$42</span></div>
    <div>11-20...lights : <span>$45</span></div>
    <div class="right">40 and over &nbsp;: <span>$40</span></div>
  </div>
  <p class="sheet-url">www.brinholt.com.au</p>
</section>

<section class="page back">
  <div class="back-band"></div>
  <div class="back-backdrop" role="img" aria-label="Teal-toned photo of a bedroom lit by downlights"></div>
  <div class="brand-name"><span class="mark"></span>brinholt</div>
  <p class="back-url">www.brinholt.com.au</p>
</section>

</body>
</html>
```